Business Card Design

I need a business card for a new company based in Australia called "MedLinkora".

Its a cloud program for GPs that allows them to search for the specialist they require using a simple user friendly tool.

I would like the colours to match those in the program (the colours in the logo attached).

The final design should reflect the programs clarity, ease of use and professionalism.

Target Market(s)

GPs and other Health Professionals

Industry/Entity Type

Business

Contact Information for Business Card

MedLinkora; The Whole Consultant Index; Marla Voss CEO; 0438215967; marla@medlinkora.example; www.medlinkora.example

Requirements
Must have
• Must have the logo attached; the web address and my name and phone number
Nice to have
• the slogan "The Whole Consultant Index"

```html
<!DOCTYPE html>
<html lang="en">
<head>
<meta charset="utf-8">
<title>MedLinkora Business Card</title>
<link rel="stylesheet" href="https://fonts.googleapis.com/css2?family=Open+Sans:wght@400;600;700&family=Questrial&display=swap">
<style>
  :root {
    --brand-blue: #1aaee2;
    --swoosh-grey: #9a9a9c;
    --tagline-grey: #7d7d80;
    --ink: #2e2e30;
    --card-white: #ffffff;
    --backdrop: #e9e9eb;
  }
  * { margin: 0; padding: 0; box-sizing: border-box; }
  html, body {
    width: 1200px; height: 1200px; overflow: hidden;
    background: var(--backdrop);
  }
  .canvas {
    width: 1200px; height: 1200px;
    display: flex; flex-direction: column; align-items: center; justify-content: center;
    gap: 60px;
  }
  .card {
    position: relative;
    width: 900px; height: 515px;
    background: var(--card-white);
    border-radius: 42px;
    overflow: hidden;
    box-shadow: 0 6px 18px rgba(0,0,0,0.12);
  }
  .brand {
    position: absolute;
    font-family: "Questrial", sans-serif;
  }
  .brand-name {
    display: block;
    font-size: 108px; line-height: 1;
    color: var(--brand-blue);
    letter-spacing: -1px;
  }
  .brand-tagline {
    display: block;
    margin-top: 2px;
    font-size: 31px;
    color: var(--tagline-grey);
    letter-spacing: 0.5px;
  }
  .card-front .brand { left: 160px; top: 70px; }
  .card-back .brand { left: 175px; top: 110px; }

  .front-art { position: absolute; inset: 0; }

  .person {
    position: absolute; right: 505px; top: 262px;
    text-align: right;
    font-family: "Open Sans", sans-serif;
  }
  .person-name { font-size: 29px; font-weight: 700; color: var(--brand-blue); }
  .person-role { font-size: 21px; color: var(--tagline-grey); margin-top: 4px; }

  .divider {
    position: absolute; left: 418px; top: 250px;
    width: 1.5px; height: 95px; background: #c8c8ca;
  }
  .contact {
    position: absolute; left: 438px; top: 252px;
    font-family: "Open Sans", sans-serif;
    font-size: 25px; color: var(--ink);
    list-style: none;
  }
  .contact li { display: flex; align-items: center; gap: 10px; height: 44px; }
  .contact svg { width: 24px; height: 24px; flex: none; }

  .web {
    font-family: "Open Sans", sans-serif;
    letter-spacing: 2px;
  }
  .card-front .web {
    position: absolute; left: 0; right: 0; bottom: 30px;
    text-align: center; font-size: 27px; color: var(--card-white);
  }
  .card-back .web {
    position: absolute; left: 0; right: 0; top: 330px;
    text-align: center; font-size: 32px; color: var(--ink);
  }
</style>
</head>
<body>
<main class="canvas">

  <section class="card card-front" aria-label="Business card front">
    <svg class="front-art" viewBox="0 0 900 515" width="900" height="515" aria-hidden="true">
      <path d="M0,338 Q330,382 690,396 Q330,400 0,372 Z" fill="var(--swoosh-grey)"/>
      <path d="M0,368 Q430,450 900,352 L900,515 L0,515 Z" fill="var(--brand-blue)"/>
    </svg>

    <div class="brand">
      <span class="brand-name">MedLinkora</span>
      <span class="brand-tagline">The Whole Consultant Index</span>
    </div>

    <div class="person">
      <p class="person-name">Marla Voss</p>
      <p class="person-role">CEO</p>
    </div>

    <div class="divider"></div>

    <ul class="contact">
      <li>
        <svg viewBox="0 0 24 24" aria-hidden="true">
          <circle cx="12" cy="12" r="11" fill="none" stroke="var(--brand-blue)" stroke-width="1.8"/>
          <path d="M8.5 6.5c1 0 1.6 2.2 1.1 2.8l-.8.9c.6 1.5 1.7 2.7 3.2 3.4l.9-.8c.6-.5 2.8.1 2.8 1.1 0 1.4-1.2 2.4-2.6 2.1-3.3-.8-6-3.5-6.7-6.8-.3-1.4.7-2.7 2.1-2.7z" fill="var(--brand-blue)"/>
        </svg>
        <span>0438215967</span>
      </li>
      <li>
        <svg viewBox="0 0 24 24" aria-hidden="true">
          <path d="M2 10 L12 3 L22 10 V21 H2 Z" fill="var(--brand-blue)"/>
          <path d="M2 10 L12 16 L22 10" fill="none" stroke="#fff" stroke-width="1.6"/>
        </svg>
        <span>marla@medlinkora.example</span>
      </li>
    </ul>

    <p class="web">www.medlinkora.example</p>
  </section>

  <section class="card card-back" aria-label="Business card back">
    <div class="brand">
      <span class="brand-name">MedLinkora</span>
      <span class="brand-tagline">The Whole Consultant Index</span>
    </div>
    <p class="web">www.medlinkora.example</p>
  </section>

</main>
</body>
</html>
```